Logo and Card design for KRV Home Solutions LLC

I need an edgier logo and business card designs. Current logo attached. I like the colors below. I would like the logo to incorporate a home in the design.
Title = Principal-Acquisitions
Email:KRVHOMESOLUTIONS@fernmail.example
555-214-0937
facebook
IG
2 sided business card with the front being contact info a slogan about selling a home fast. The back incorporating What we do. Buy houses, land, or commercial property as is. We find solutions to make the process of selling simple and fair.

Target Market(s)

Motivated house sellers.

Industry/Entity Type

Business

Contact Information for Business Card

Who we are: We are a Faith based Real Estate Investment Company. We pay cash for homes in any condition and can close quick. Whatever the reason you need to sell fast, we can help. We believe in creating win-win solutions to help you in your time of need. We care! We can help!

Logo Text

KRV Home Solutions LLC

Font styles to use
Sans Serif

Colors
33a6d7
0355a3
85abd2
cee9f5
9d9d9d
b2b2b2
ffffff

Requirements
Must have
• Old logo attached. I want something edgier.
• Company name, phone number, description on the back of what we can do. Pay all cash. Buy in as is condition. No fees,Commisions or closing costs.Close quick. No hassles with solutions to meet your unique situation.
• Call today for an offer within 24 hours.

```html
<!DOCTYPE html>
<html lang="en">
<head>
<meta charset="utf-8">
<title>KRV Home Solutions LLC — Business Card</title>
<link rel="stylesheet" href="https://fonts.googleapis.com/css2?family=Roboto:wght@400;500;700&family=Roboto+Condensed:wght@400;700&display=swap">
<style>
  :root {
    --navy: #1d3a7a;
    --blue: #0355a3;
    --slate: #5c5c5c;
    --grey: #9d9d9d;
    --ink: #4a4a4a;
    --paper: #ffffff;
    --stage: #e9ebee;
    --photo-top: #eef1f4;
    --photo-bottom: #dfe5e4;
  }
  * { margin: 0; padding: 0; box-sizing: border-box; }
  html, body { width: 1200px; height: 886px; overflow: hidden; }
  body {
    background: var(--stage);
    font-family: "Roboto", Arial, sans-serif;
    display: flex;
    align-items: center;
    justify-content: center;
    gap: 30px;
  }
  .card {
    position: relative;
    width: 560px;
    height: 320px;
    background: var(--paper);
    overflow: hidden;
    box-shadow: 0 6px 18px rgba(0,0,0,0.18);
  }
  /* Front */
  .card-front .house-photo {
    position: absolute; left: 0; top: 0; width: 340px; height: 240px;
    background: linear-gradient(170deg, var(--photo-top) 0%, var(--photo-bottom) 100%);
  }
  .card-front .shapes { position: absolute; inset: 0; }
  .brand-name {
    position: absolute; left: 30px; top: 138px;
    display: flex; align-items: center; gap: 10px;
    color: var(--navy);
    font-family: "Roboto Condensed", Arial, sans-serif;
    font-weight: 700; font-size: 24px; line-height: 1.05; letter-spacing: 0.5px;
  }
  .brand-name .mark { width: 16px; height: 16px; background: var(--navy); flex: none; }
  .brand-name .lines { display: flex; flex-direction: column; }
  .person {
    position: absolute; right: 24px; top: 28px; text-align: right; color: #fff;
  }
  .person .name { font-family: "Roboto Condensed", Arial, sans-serif; font-weight: 700; font-size: 23px; letter-spacing: 0.5px; }
  .person .title { font-size: 14px; margin-top: 3px; }
  .contacts {
    position: absolute; right: 24px; top: 122px; list-style: none;
    color: #fff; font-size: 13px; text-align: right; line-height: 21px;
  }
  .contacts li { display: flex; justify-content: flex-end; align-items: center; gap: 8px; }
  .contacts svg { width: 12px; height: 12px; fill: #fff; }
  .offer-list {
    position: absolute; left: 40px; top: 238px; color: #fff;
    font-size: 12px; line-height: 15px; padding-left: 12px;
  }
  .offer-list li { margin-bottom: 1px; }
  /* Back */
  .card-back { padding: 26px 40px; text-align: center; color: var(--ink); }
  .back-brand {
    color: var(--blue); font-family: "Roboto Condensed", Arial, sans-serif;
    font-weight: 700; font-size: 28px; letter-spacing: 1px;
  }
  .rule { width: 300px; height: 2px; background: var(--grey); margin: 12px auto 14px; }
  .section-title { color: var(--blue); font-weight: 700; font-size: 13px; letter-spacing: 0.5px; margin-bottom: 5px; }
  .section-text { font-size: 12px; line-height: 16px; margin-bottom: 12px; }
</style>
</head>
<body>
  <section class="card card-front" aria-label="Business card front">
    <div class="house-photo" role="img" aria-label="Faded photograph of a large family house"></div>
    <svg class="shapes" viewBox="0 0 560 320" aria-hidden="true">
      <polygon points="300,20 560,20 560,92 278,92" fill="var(--slate)"/>
      <polygon points="278,92 560,92 560,320 0,320 0,228 232,228" fill="var(--navy)"/>
    </svg>
    <div class="brand-name"><span class="mark"></span><span class="lines"><span>KRV HOME</span><span>SOLUTIONS</span></span></div>
    <div class="person">
      <div class="name">JORDAN VALE</div>
      <div class="title">Principal-Acquisitions</div>
    </div>
    <ul class="contacts">
      <li>555-214-0937
        <svg viewBox="0 0 24 24"><path d="M6.6 10.8a15 15 0 0 0 6.6 6.6l2.2-2.2c.3-.3.7-.4 1-.2 1.1.4 2.3.6 3.6.6.6 0 1 .4 1 1V20c0 .6-.4 1-1 1A17 17 0 0 1 3 4c0-.6.4-1 1-1h3.5c.6 0 1 .4 1 1 0 1.3.2 2.5.6 3.6.1.3 0 .7-.2 1z"/></svg></li>
      <li>KRVHOMESOLUTIONS@fernmail.example
        <svg viewBox="0 0 24 24"><path d="M2 5h20v14H2z M3 6l9 7 9-7" fill="none" stroke="#fff" stroke-width="2"/></svg></li>
      <li>KRVHOMESOLUTIONS.example
        <svg viewBox="0 0 24 24"><circle cx="12" cy="12" r="10" fill="none" stroke="#fff" stroke-width="2"/><path d="M2 12h20M12 2c3 3 3 17 0 20M12 2c-3 3-3 17 0 20" fill="none" stroke="#fff" stroke-width="1.5"/></svg></li>
    </ul>
    <ul class="offer-list">
      <li>Pay all cash. Buy in as is condition</li>
      <li>No fees,Commisions or closing costs</li>
      <li>Close quick. No hassles with solutions to meet your unique situation</li>
      <li>Call today for an offer within 24 hours</li>
    </ul>
  </section>

  <section class="card card-back" aria-label="Business card back">
    <div class="back-brand">KRV HOME SOLUTIONS</div>
    <div class="rule"></div>
    <h2 class="section-title">WHO WE ARE</h2>
    <p class="section-text">We are a Faith based Real Estate Investment Company. We pay cash for homes in any condition and can close quick. Whatever the reason you need to sell fast, we can help. We believe in creating win-win solutions to help you in your time of need.</p>
    <h2 class="section-title">WHAT WE DO</h2>
    <p class="section-text">Buy houses, land, or commercial property as is.<br>We find solutions to make the process of selling simple and fair.</p>
  </section>
</body>
</html>
```